Business Card Design

This is a new cafe in Wavell Heights.
My mantra / (updated) slogan is 'Nourishing Food. Coffee as its Best'
95% of food is produced from my own kitchen.
Breakfast and lunch items on the menu include lots of good stuff on sourdough, all natural smoothies, gluten/dairy free foods/treats as well as more traditional fare. Focus is on wholesome healthy food and fantastic coffee.
Colours are predominantly green from attached logo and black but happy for some coffee bean brown for effect.
Preferred font would be Dilennial UPC per attached logo / flyer.
We have a Chatterly page and Pictura account.

Industry/Entity Type

Business

Contact Information for Business Card

Meredith Tallis
Lumen Cafe
384 Pelling Street
Alderwood Vale QLD 4099

```html
<!DOCTYPE html>
<html lang="en">
<head>
<meta charset="utf-8">
<title>Lumen Cafe – Business Card</title>
<link rel="stylesheet" href="https://fonts.googleapis.com/css2?family=Tinos:wght@400;700&display=swap">
<style>
  :root {
    --backdrop: #e9e6e1;
    --card: #ffffff;
    --green: #4cb84f;
    --green-light: #6fcd6c;
    --charcoal: #3a3a3a;
    --ink: #1f1f1f;
  }
  * { box-sizing: border-box; margin: 0; padding: 0; }
  html, body { width: 1200px; height: 902px; overflow: hidden; }
  body {
    background: var(--backdrop);
    font-family: "Tinos", "Times New Roman", serif;
    display: flex;
    align-items: center;
    justify-content: center;
    gap: 40px;
  }
  .card {
    position: relative;
    width: 540px;
    height: 310px;
    background: var(--card);
    box-shadow: 0 6px 18px rgba(0,0,0,.18);
    overflow: hidden;
  }
  .card-art { position: absolute; inset: 0; }
  .brand {
    position: absolute;
    display: flex;
    align-items: center;
    gap: 10px;
    color: var(--ink);
    font-weight: 400;
    white-space: nowrap;
  }
  .brand-dot {
    width: 22px; height: 22px;
    border-radius: 50%;
    background: var(--green);
  }
  .card-front .brand { left: 190px; top: 150px; font-size: 52px; }
  .card-back .brand { left: 40px; top: 128px; font-size: 40px; }
  .brand-dot-small { width: 16px; height: 16px; }
  .social-line {
    position: absolute;
    right: 26px; top: 18px;
    font-size: 15px;
    color: var(--ink);
  }
  .details {
    position: absolute;
    left: 40px; top: 188px;
    font-size: 15px;
    line-height: 1.32;
    color: var(--ink);
    list-style: none;
  }
  .details .highlight { color: var(--green); letter-spacing: .5px; }
</style>
</head>
<body>
  <section class="card card-front" aria-label="Card front">
    <svg class="card-art" viewBox="0 0 540 310" aria-hidden="true">
      <defs>
        <linearGradient id="frontGreen" x1="0" y1="0" x2="1" y2="1">
          <stop offset="0" stop-color="var(--green)"/>
          <stop offset="1" stop-color="var(--green-light)"/>
        </linearGradient>
      </defs>
      <path d="M0 0 H540 V2 C330 12 160 110 66 310 H0 Z" fill="url(#frontGreen)"/>
      <path d="M525 10 C335 26 178 122 94 310" fill="none" stroke="var(--charcoal)" stroke-width="14"/>
    </svg>
    <div class="brand"><span class="brand-dot"></span>Lumen Cafe</div>
  </section>

  <section class="card card-back" aria-label="Card back">
    <svg class="card-art" viewBox="0 0 540 310" aria-hidden="true">
      <defs>
        <linearGradient id="backGreen" x1="0" y1="0" x2="1" y2="0">
          <stop offset="0" stop-color="var(--green)"/>
          <stop offset="1" stop-color="var(--green-light)"/>
        </linearGradient>
      </defs>
      <path d="M0 0 H540 V78 C380 58 180 70 0 118 Z" fill="url(#backGreen)"/>
      <path d="M0 118 C180 70 380 58 540 78 V96 C380 74 190 84 0 124 Z" fill="var(--charcoal)"/>
    </svg>
    <p class="social-line">Find us on Chatterly and Pictura</p>
    <div class="brand"><span class="brand-dot brand-dot-small"></span>Lumen Cafe</div>
    <ul class="details">
      <li>Nourishing food from the heart, Coffee at its best.</li>
      <li>384 Pelling Street Alderwood Vale QLD 4099</li>
      <li class="highlight">OPEN FOR AFTER-SCHOOL MUNCHIES</li>
      <li>Milkshakes, Frappes, All-natural Smoothies</li>
      <li>Home-made burgers, Salads and Gourmet Sandwiches</li>
    </ul>
  </section>
</body>
</html>
```